Summit Builders Web Site / Business Cards

Construction Company that specializes in Water and Fire Damage, Residential ReModels, Landscaping and Building ADU (Accessory Dwelling Unit)

Growing and changing families often need additional space, and a remodeling project can often provide that. Adding a new area, or repurposing an existing one can satisfy this requirement.

Other times, homeowners want to update the look in their kitchen or bathroom with more than just a change of cabinetry or vanity doors and drawers. Whatever your needs are, Summit Builders has skilled workers who are bonded and insured, and ready to make your dreams and visions a reality.

Target Market(s)

Home Owners

Industry/Entity Type

Construction Company

Contact Information for Business Card

Center Logo with our information on the corners

Back side to be Logo Only
Contact Info
CSLB License # 2418596
info@summitbuildersca.example
www.summitbuildersca.example

Coding

Coded - Design and coding required

Number of Pages Required

5+ page

Font styles to use
Serif
Sans Serif

Requirements
Must have
• Using our Logo Colors
Home
About Us
Services
Projects / Portfolio
Contact Us
Nice to have
• Colors matching our Logo
Should not have
• Black because it doesnt match our logo

```html
<!DOCTYPE html>
<html lang="en">
<head>
<meta charset="utf-8">
<title>Summit Builders — Home</title>
<link href="https://fonts.googleapis.com/css2?family=Poppins:wght@300;400;500;600;700&display=swap" rel="stylesheet">
<style>
:root{
  --orange:#f26a0f;
  --deep:#1f2a34;
  --deep-line:#3a4652;
  --ink:#1b1b1b;
  --muted:#8a8a8a;
  --soft:#c3ccd4;
  --light:#f3f3f3;
  --white:#ffffff;
}
*{margin:0;padding:0;box-sizing:border-box}
html,body{width:1200px;height:3615px;overflow:hidden}
body{position:relative;font-family:'Poppins',sans-serif;color:var(--ink);background:var(--white)}
.abs{position:absolute}
.ph{position:absolute}
/* top bar */
.topbar{left:0;top:0;width:1200px;height:38px;background:var(--deep);color:var(--white);font-size:12px}
.topbar-inner{position:absolute;right:161px;top:0;height:38px;display:flex;align-items:stretch}
.topbar .item{display:flex;align-items:center;gap:8px;padding:0 18px;white-space:nowrap;border-right:1px solid var(--deep-line)}
.topbar .item:last-of-type{border-right:0}
.topbar .iso span{color:var(--orange)}
.quote-btn{width:113px;background:var(--orange);color:var(--white);font-size:12px;display:flex;align-items:center;justify-content:center;letter-spacing:.3px;white-space:nowrap}
/* header */
.header{left:0;top:38px;width:1200px;height:74px;background:var(--white)}
.brand{position:absolute;left:160px;top:-38px;width:112px;height:112px;background:var(--white);display:flex;flex-direction:column;align-items:center;justify-content:center;gap:6px}
.brand-mark{width:20px;height:20px;background:var(--orange)}
.brand-name{font-size:15px;font-weight:600;color:var(--ink);letter-spacing:.5px;text-align:center;line-height:1.1}
.nav a{position:absolute;top:28px;font-size:11px;color:#777;text-decoration:none;letter-spacing:.4px;text-transform:uppercase;white-space:nowrap}
.nav a.active{color:var(--orange)}
.nav a.active::after{content:"";position:absolute;left:0;right:0;top:43px;height:2px;background:var(--orange)}
/* hero */
.hero{left:0;top:112px;width:1200px;height:638px;background:linear-gradient(120deg,#6e6458 0%,#8f8376 35%,#b4ab9f 60%,#7a7067 100%)}
.hero-shade{position:absolute;inset:0;background:rgba(20,15,10,.28)}
.hero-box{position:absolute;left:413px;top:225px;width:374px;height:188px;background:rgba(242,106,15,.88)}
.hero-title{position:absolute;left:0;width:1200px;top:258px;text-align:center;color:var(--white);font-size:44px;font-weight:600;line-height:57px;text-shadow:0 2px 6px rgba(0,0,0,.45)}
.round-arrow{position:absolute;width:44px;height:44px;border-radius:50%;background:rgba(255,255,255,.75);display:flex;align-items:center;justify-content:center}
/* generic */
h2.sec{position:absolute;font-weight:400;font-size:27px;line-height:35px;color:var(--ink)}
p.body{position:absolute;font-size:11px;line-height:19px;color:var(--muted)}
.btn{position:absolute;background:var(--orange);color:var(--white);font-size:12px;display:flex;align-items:center;justify-content:center;gap:10px;letter-spacing:.3px;text-transform:uppercase}
/* services */
.svc-band{left:0;top:1193px;width:1039px;height:547px;background:var(--deep)}
.svc-title{position:absolute;font-size:16px;color:var(--orange)}
.svc-text{position:absolute;font-size:10.5px;line-height:19px;color:var(--white);width:272px}
.svc-text.on-white{color:var(--muted)}
/* featured */
.proj-card{left:291px;top:2250px;width:188px;height:135px;background:var(--orange);color:var(--white);text-align:center;padding-top:26px}
.proj-card h3{font-weight:400;font-size:16px;margin-bottom:8px}
.proj-card p{font-size:10px;line-height:18px;padding:0 18px}
.ring-arrow{position:absolute;width:42px;height:42px;border-radius:50%;border:1px solid #e4e4e4;background:var(--white);display:flex;align-items:center;justify-content:center}
/* stats */
.stats{left:0;top:2445px;width:1200px;height:397px;background:var(--light)}
.stat{position:absolute;width:203px;height:112px;background:var(--white);border:1px solid #e8e8e8;text-align:center;padding-top:20px}
.stat b{display:block;font-size:34px;font-weight:600;color:var(--orange);line-height:40px}
.stat span{display:block;font-size:12px;color:#555;letter-spacing:.5px;margin-top:4px}
/* testimonial */
.quote-text{left:355px;top:3052px;width:491px;text-align:center;font-size:10.5px;line-height:19.5px;color:#666}
.author{left:0;width:1200px;top:3140px;text-align:center;font-size:12px;color:var(--orange)}
/* footer */
.footer{left:0;top:3217px;width:1200px;height:398px;background:var(--deep)}
.foot-h{position:absolute;font-size:19px;color:var(--orange);text-align:center;width:400px}
.foot-t{position:absolute;text-align:center;width:400px;font-size:11.5px;line-height:19px;color:var(--white)}
.foot-t.dim{color:var(--soft);font-size:10.5px}
.news-field{position:absolute;left:707px;top:3386px;width:225px;height:38px;border-radius:19px;background:var(--white);font-size:11px;color:#aaa;padding:11px 0 0 13px}
.news-go{position:absolute;right:4px;top:4px;width:30px;height:30px;border-radius:50%;background:var(--orange);display:flex;align-items:center;justify-content:center}
.social{position:absolute;top:3534px;width:32px;height:32px;background:var(--orange)}
</style>
</head>
<body>

<!-- top bar -->
<div class="abs topbar">
  <div class="topbar-inner">
    <div class="item iso"><span>ISO</span> 9001 : 2017</div>
    <div class="item">
      <svg width="14" height="10" viewBox="0 0 14 10"><rect x="0.5" y="0.5" width="13" height="9" fill="none" stroke="#f26a0f"/><path d="M0.5 0.5 L7 6 L13.5 0.5" fill="none" stroke="#f26a0f"/></svg>
      info@summitbuildersca.example
    </div>
    <div class="item">
      <svg width="12" height="12" viewBox="0 0 24 24"><path d="M6.6 10.8a15 15 0 0 0 6.6 6.6l2.2-2.2c.3-.3.7-.4 1-.2 1.1.4 2.3.6 3.6.6.6 0 1 .4 1 1V20c0 .6-.4 1-1 1A17 17 0 0 1 3 4c0-.6.4-1 1-1h3.5c.6 0 1 .4 1 1 0 1.3.2 2.5.6 3.6.1.3 0 .7-.2 1z" fill="#f26a0f"/></svg>
      +1 555 014 2287
    </div>
    <div class="quote-btn">GET A QUOTE</div>
  </div>
</div>

<!-- header -->
<div class="abs header">
  <div class="brand">
    <div class="brand-mark"></div>
    <div class="brand-name">Summit<br>Builders</div>
  </div>
  <nav class="nav">
    <a class="active" style="left:564px">Home</a>
    <a style="left:626px">About</a>
    <a style="left:693px">Services</a>
    <a style="left:778px">Portfolio / Projects</a>
    <a style="left:943px">Contact</a>
  </nav>
  <svg class="abs" style="left:1022px;top:28px" width="17" height="17" viewBox="0 0 17 17"><circle cx="7" cy="7" r="5.5" fill="none" stroke="#f26a0f" stroke-width="1.6"/><path d="M11 11 L16 16" stroke="#f26a0f" stroke-width="1.6"/></svg>
</div>

<!-- hero -->
<section class="abs hero" role="img" aria-label="Photo of two builders reviewing plans inside a house under renovation">
  <div class="hero-shade"></div>
  <div class="hero-box"></div>
  <h1 class="hero-title">THE BEST CHOOSE US<br>BECAUSE WE DELIVER</h1>
  <div class="round-arrow" style="left:138px;top:297px"><svg width="10" height="14" viewBox="0 0 10 14"><path d="M8 1 L2 7 L8 13" fill="none" stroke="#f26a0f" stroke-width="1.5"/></svg></div>
  <div class="round-arrow" style="left:1017px;top:297px"><svg width="10" height="14" viewBox="0 0 10 14"><path d="M2 1 L8 7 L2 13" fill="none" stroke="#555" stroke-width="1.5"/></svg></div>
</section>

<!-- experience -->
<h2 class="sec" style="left:161px;top:805px">Experience the change<br>with us</h2>
<p class="body" style="left:161px;top:888px;width:430px">Lorem ipsum dolor sit amet, consectetur adipiscing elit, sed do eiusmod tempor incididunt ut labore et dolore magna aliqua. Ut enim ad minim veniam, quis nostrud exercitation ullamco laboris nisi ut aliquip ex ea commodo consequat. Duis aute irure dolor in reprehenderit in voluptate velit esse cillum.</p>
<div class="btn" style="left:161px;top:991px;width:135px;height:43px">Learn more
  <svg width="16" height="8" viewBox="0 0 16 8"><path d="M0 4 H14 M11 1 L14 4 L11 7" fill="none" stroke="#fff" stroke-width="1.3"/></svg></div>
<div class="ph" style="left:769px;top:839px;width:270px;height:195px;background:linear-gradient(160deg,#e9e9e9,#c8c2bb 60%,#e07a2e 100%)" role="img" aria-label="Photo of an engineer in a hard hat and safety vest on site"></div>
<div class="ph" style="left:664px;top:810px;width:269px;height:194px;background:linear-gradient(180deg,#9aa0a3 0%,#b5735a 55%,#6d7250 100%)" role="img" aria-label="Photo of firefighters at a burning brick house"></div>

<!-- services -->
<div class="abs svc-band"></div>
<div class="ph" style="left:161px;top:1103px;width:270px;height:194px;background:linear-gradient(180deg,#8e969c 0%,#b3a08a 55%,#6b4a36 100%)" role="img" aria-label="Photo of a new home under construction with timber framing"></div>
<div class="svc-title" style="left:162px;top:1318px">Home Construction</div>
<div class="svc-text" style="left:162px;top:1347px">Lorem ipsum dolor sit amet, consectet adipiscing elit, sed do eiusmod tempor incididunt.</div>

<div class="ph" style="left:487px;top:1238px;width:270px;height:194px;background:linear-gradient(160deg,#5a6f8e 0%,#9a8a78 50%,#c8742e 100%)" role="img" aria-label="Photo of people discussing a small house model on a desk"></div>
<div class="svc-title" style="left:489px;top:1453px">Building Remodeling</div>
<div class="svc-text" style="left:489px;top:1482px">Lorem ipsum dolor sit amet, consectet adipiscing elit, sed do eiusmod tempor incididunt.</div>

<div class="ph" style="left:161px;top:1426px;width:270px;height:194px;background:linear-gradient(180deg,#f2f2f0 0%,#d9d7d3 60%,#8b7257 100%)" role="img" aria-label="Photo of a bright white kitchen with a wooden dining table"></div>
<div class="svc-title" style="left:162px;top:1641px">Interior Design</div>
<div class="svc-text" style="left:162px;top:1670px">Lorem ipsum dolor sit amet, consectet adipiscing elit, sed do eiusmod tempor incididunt.</div>

<div class="ph" style="left:487px;top:1561px;width:270px;height:193px;background:linear-gradient(180deg,#d4d0c8 0%,#b89a72 55%,#5b3b25 100%)" role="img" aria-label="Photo of a renovated small cabin interior with a ladder and kitchenette"></div>
<div class="svc-title" style="left:489px;top:1776px">Renovation</div>
<div class="svc-text on-white" style="left:489px;top:1805px">Lorem ipsum dolor sit amet, consectet adipiscing elit, sed do eiusmod tempor incididunt.</div>

<h2 class="sec" style="left:811px;top:1330px;color:#fff">Our Services</h2>
<p class="body" style="left:811px;top:1380px;width:195px;color:#fff;font-size:10.5px">Lorem ipsum dolor sit aconsectetur adipiscing elit, sed do eius tempor incididunt ut labore et dolore magna aliqua.</p>
<div class="btn" style="left:810px;top:1482px;width:135px;height:44px">Learn more
  <svg width="16" height="8" viewBox="0 0 16 8"><path d="M0 4 H14 M11 1 L14 4 L11 7" fill="none" stroke="#fff" stroke-width="1.3"/></svg></div>

<!-- featured projects -->
<h2 class="sec" style="left:162px;top:1893px">Featured Projects</h2>
<p class="body" style="left:162px;top:1945px;width:335px;font-size:12.5px;line-height:23px;color:#6d6d6d">Lorem ipsum dolor sit amet, consectetur adipiscing elit, sed do eiusmod tempor incididunt ut labore et dolore magna aliqua.</p>
<div class="ph" style="left:385px;top:2039px;width:525px;height:301px;background:linear-gradient(180deg,#3e6aa3 0%,#6f8fb5 35%,#7a4a2c 60%,#3f5a2a 100%)" role="img" aria-label="Photo of a modern home with timber cladding and a white garage at dusk"></div>
<div class="ring-arrow" style="left:161px;top:2169px"><svg width="10" height="14" viewBox="0 0 10 14"><path d="M8 1 L2 7 L8 13" fill="none" stroke="#f26a0f" stroke-width="1.5"/></svg></div>
<div class="ring-arrow" style="left:995px;top:2169px"><svg width="10" height="14" viewBox="0 0 10 14"><path d="M2 1 L8 7 L2 13" fill="none" stroke="#f26a0f" stroke-width="1.5"/></svg></div>
<div class="abs proj-card">
  <h3>Project Name</h3>
  <p>Lorem ipsum dolor sit amet, consectet adipiscing elit, incididunt.</p>
</div>

<!-- stats -->
<section class="abs stats"></section>
<div class="stat" style="left:161px;top:2505px"><b>53</b><span>TOTAL PROJECTS</span></div>
<div class="stat" style="left:386px;top:2535px"><b>15</b><span>WORKING IN STATES</span></div>
<div class="stat" style="left:161px;top:2640px"><b>371</b><span>STAFF MEMBERS</span></div>
<div class="stat" style="left:386px;top:2670px"><b>2,600</b><span>HOURS FOR WORK</span></div>
<h2 class="sec" style="left:706px;top:2568px">We Deliver Landmark<br>Projects</h2>
<p class="body" style="left:706px;top:2652px;width:310px;font-size:10.5px">We are rethoric question ran over her cheek When she reached the first hills of the Italic Mountains, she had a last view back on the skyline of her hometown Bookmarks grove, the headline of Alphabet Village and the subline of her own road, the Line Lane.</p>

<!-- testimonials -->
<h2 class="sec" style="left:0;width:1200px;top:2898px;text-align:center;font-size:30px;line-height:40px">Client's Testimonials</h2>
<div class="abs" style="left:546px;top:2976px;width:56px;height:56px;border-radius:50%;background:var(--orange);display:flex;align-items:center;justify-content:center;color:#fff;font-size:34px;font-weight:700;line-height:1;padding-top:14px">&ldquo;</div>
<div class="ph" style="left:591px;top:2976px;width:56px;height:56px;border-radius:50%;background:linear-gradient(160deg,#c9d3db,#6b7f92);border:3px solid #fff" role="img" aria-label="Portrait photo of the client"></div>
<svg class="abs" style="left:304px;top:3061px" width="16" height="40" viewBox="0 0 16 40"><path d="M14 1 L3 20 L14 39" fill="none" stroke="#f26a0f" stroke-width="1.3"/></svg>
<svg class="abs" style="left:880px;top:3061px" width="16" height="40" viewBox="0 0 16 40"><path d="M2 1 L13 20 L2 39" fill="none" stroke="#555" stroke-width="1.3"/></svg>
<p class="abs quote-text">Lorem ipsum dolor sit amet, consectetur adipiscing elit, sed do eiusmod tempor incididunt ut labore et dolore magna aliqua. Ut enim ad minim veniam, quis nostrud exercitation ullamco laboris nisi ut aliquip ex ea commodo consequat. Duis aute irure dolor in reprehenderit in voluptate velit esse cillum dolore eu fugiat nulla pariatur.</p>
<div class="abs author">- Clara M</div>

<!-- footer -->
<footer class="abs footer"></footer>
<div class="abs" style="left:599px;top:3277px;width:1px;height:180px;background:var(--deep-line)"></div>
<div class="abs" style="left:161px;top:3457px;width:878px;height:1px;background:var(--deep-line)"></div>

<div class="foot-h" style="left:180px;top:3272px">Contact Information</div>
<div class="foot-t" style="left:180px;top:3320px">Jordan Marlow | Branch Manager</div>
<div class="foot-t dim" style="left:180px;top:3350px">1420 Orchard Ave Suite 3 Tustin, CA 92780</div>
<div class="foot-t dim" style="left:180px;top:3374px">info@summitbuildersca.example</div>
<div class="foot-t" style="left:180px;top:3398px;font-size:18px;line-height:24px">+1 555 014 2287</div>

<div class="foot-h" style="left:620px;top:3272px">Newsletter Sign Up</div>
<div class="foot-t" style="left:620px;top:3320px;font-size:11px">Enter Your email address and receive<br>latest news and offers!!!</div>
<div class="news-field">Email Address
  <div class="news-go"><svg width="10" height="12" viewBox="0 0 10 12"><path d="M1 1 L9 6 L1 11 Z" fill="#fff"/></svg></div>
</div>

<div class="foot-t dim" style="left:400px;top:3500px">Copyright © 2020 Summit Builders - All Right Reserved.</div>
<div class="social" style="left:528px" aria-label="Social link"></div>
<div class="social" style="left:566px" aria-label="Social link"></div>
<div class="social" style="left:604px" aria-label="Social link"></div>
<div class="social" style="left:642px" aria-label="Social link"></div>

</body>
</html>
```